Expedition Cruise Sales Website for the Polar Regions (Antarctica & Arctic)

This will be a website for selling cruises.
This site should have a homepage, a ship page, destinations, and itineraries.
I have created a file specifying each page, and it is attached.
Pages:
1. Home
2. Cruise Lines
- 2.1 Ships
3. Destinations
- 3.1 Region - 3.2 Country - 3.3 City
4. Itineraries
- 4.1 Itinerary
5. Blog / Travel Tips 6. About Us
7. Contact
Please take a look on the attached pdf
Target Market(s)
Expedition Travelers
Coding
Coded - Design and coding required
Number of Pages Required
5+ page
Font styles to use
Look and feel
Each slider illustrates characteristics of the customer's brand and the style your logo design should communicate.

```html
<!DOCTYPE html>
<html lang="en">
<head>
<meta charset="utf-8">
<title>Glacia.co – Selling Cruises</title>
<link rel="stylesheet" href="https://fonts.googleapis.com/css2?family=Josefin+Sans:wght@400;600;700&family=Montserrat:wght@400;500;600&display=swap">
<style>
:root{
  --blue:#3a74b8;
  --blue-bright:#2f6fc0;
  --navy:#2e4566;
  --ink:#22324a;
  --deep:#16243a;
  --pale:#e9f0f7;
  --white:#ffffff;
  --text:#2b2b2b;
  --star:#f5b400;
  --green:#2fb54a;
}
*{box-sizing:border-box;margin:0;padding:0}
html,body{width:1200px;height:4203px;overflow:hidden}
body{position:relative;font-family:"Montserrat",sans-serif;color:var(--text);background:var(--white)}
.abs{position:absolute}
.caps{font-family:"Josefin Sans",sans-serif;font-variant:small-caps;font-weight:600;letter-spacing:.04em}
.dot{width:22px;height:22px;border-radius:50%;background:var(--blue);left:589px}

/* hero */
.hero{left:0;top:0;width:1200px;height:1084px;
  background:linear-gradient(180deg,#4d7fb8 0%,#7f9cc4 14%,#c98f78 24%,#5f8fb8 34%,#2f73a8 48%,#3c77ad 70%,#4d7ea8 100%)}
.brand{left:110px;top:66px;color:var(--white);font-size:25px;font-weight:600}
.brand-dot{left:150px;top:24px;width:30px;height:30px;border-radius:50%;background:var(--white)}
.nav{top:78px;color:var(--white);font-size:13px}
.nav.active::after{content:"";position:absolute;left:0;right:0;bottom:-8px;height:3px;background:var(--navy)}
.call{left:893px;top:16px;width:44px;height:44px;border:2px solid var(--white);border-radius:50%}
.call-text{left:955px;top:18px;color:var(--white);font-size:14px;line-height:1.3}
.hero-title{right:108px;top:214px;color:var(--white);font-size:60px;text-align:right}
.hero-copy{right:120px;top:288px;width:440px;text-align:right;color:var(--white);font-size:17px;line-height:21px}
.hero-rule{left:1086px;top:290px;width:2px;height:56px;background:var(--white)}
.pill{border-radius:30px;display:flex;align-items:center;color:var(--white);font-weight:500}
.pill .ring{width:40px;height:40px;border-radius:50%;background:var(--white);border:3px solid var(--blue);margin:0 12px 0 4px;flex:none}
.hero-btn{left:792px;top:373px;width:297px;height:47px;background:var(--blue-bright);font-size:15px}

.search{left:111px;top:551px;width:976px;height:78px;background:var(--white);border-radius:40px}
.field{top:565px;height:47px;background:#d8e3ef;border-radius:24px;font-size:11px;color:#333;padding-left:16px;display:flex;align-items:center}
.search-go{left:1019px;top:561px;width:57px;height:57px;border-radius:50%;background:var(--blue-bright)}

.welcome-dot{top:706px}
.welcome-title{left:0;width:1200px;top:740px;text-align:center;font-size:40px;color:var(--white)}
.welcome-title span{color:var(--blue-bright)}
.welcome-copy{left:150px;width:900px;top:806px;text-align:center;color:var(--white);font-size:14px;line-height:26px}
.read-btn{left:518px;top:945px;width:165px;height:48px;background:var(--blue-bright);font-size:15px}

/* section heading */
.sec-title{left:0;width:1200px;text-align:center;font-size:40px;color:var(--ink)}
.sec-title span{color:var(--blue)}

/* featured cards */
.card{top:1275px;width:315px;height:481px;border-radius:30px;overflow:hidden;color:var(--white)}
.card .photo{height:282px}
.card .body{padding:18px 20px}
.card h3{font-size:21px;margin-bottom:12px}
.card p{font-size:12.5px;line-height:20px;min-height:60px}
.card .price{font-size:13px;line-height:19px;margin-top:8px}

/* destinations */
.dest-band{left:3px;top:1876px;width:1189px;height:515px;background:var(--pale)}
.dest{top:2068px;width:238px;height:238px;background:var(--white);border-radius:18px;overflow:hidden}
.dest .photo{height:183px}
.dest div.name{text-align:center;font-size:18px;padding-top:15px;color:var(--ink)}

/* cruise line */
.line-panel{left:0;top:2391px;width:663px;height:595px;background:var(--navy)}
.line-photo{left:601px;top:2466px;width:599px;height:445px;background:linear-gradient(135deg,#2c5f86,#3d7ea3 45%,#d8d4c8 55%,#2b6890 70%,#1f4f74)}
.line-title{left:110px;top:2532px;color:var(--white);font-size:40px}
.line-copy{left:114px;top:2612px;width:455px;color:var(--white);font-size:14px;line-height:25.6px}
.line-btn{left:114px;top:2839px;width:168px;height:49px;background:var(--blue-bright);font-size:15px}

/* testimonials */
.quote{top:3236px;width:475px;height:169px;background:var(--blue-bright);border-radius:85px;color:var(--white)}
.quote .face{position:absolute;left:16px;top:14px;width:142px;height:142px;border-radius:50%;background:linear-gradient(160deg,#f0ece6,#c8c0b4)}
.quote .stars{position:absolute;left:176px;top:18px;color:var(--star);font-size:20px;letter-spacing:6px}
.quote p{position:absolute;left:176px;top:48px;width:285px;font-size:11.5px;line-height:21px}
.quote .who{position:absolute;left:176px;top:114px;font-size:16px;font-weight:500}
.quote .role{position:absolute;left:176px;top:140px;font-size:11.5px}

/* footer */
.footer{left:0;top:3521px;width:1200px;height:682px;background:linear-gradient(160deg,#2b3c55 0%,#1d2c43 35%,#172437 100%)}
.foot-title{color:var(--white)}
.foot-title span{color:var(--blue-bright)}
.news-input{left:204px;top:3710px;width:604px;height:52px;background:var(--white);border-radius:26px;font-size:10px;padding-left:26px;display:flex;align-items:center;color:#333}
.news-btn{left:830px;top:3710px;width:166px;height:52px;background:var(--blue-bright);font-size:15px}
.chat{left:1007px;top:3711px;width:50px;height:50px;border-radius:50%;background:var(--green)}
.foot-brand{left:0;width:1200px;top:3938px;text-align:center;color:var(--blue);font-size:58px;font-weight:600}
.foot-nav{top:4040px;color:var(--white);font-size:13px}
.legal{top:4122px;color:var(--white);font-size:11px}
</style>
</head>
<body>

<!-- HERO -->
<div class="abs hero" role="img" aria-label="Cruise ship sailing on the open sea at sunset"></div>
<div class="abs brand-dot"></div>
<div class="abs brand">Glacia.co</div>

<div class="abs nav caps active" style="left:330px">Home</div>
<div class="abs nav caps" style="left:418px">Cruise Lines</div>
<div class="abs nav caps" style="left:553px">Destinations</div>
<div class="abs nav caps" style="left:694px">Itineraries</div>
<div class="abs nav caps" style="left:825px">Blog</div>
<div class="abs nav caps" style="left:910px">About Us</div>
<div class="abs nav caps" style="left:1027px">Contact</div>

<div class="abs call">
  <svg width="40" height="40" viewBox="0 0 40 40"><path d="M14 11c-2 1-3 3-2 6 2 5 6 9 11 11 3 1 5 0 6-2l-3-3-3 2c-3-1-6-4-7-7l2-3z" fill="none" stroke="#fff" stroke-width="1.8" stroke-linejoin="round"/></svg>
</div>
<div class="abs call-text"><span class="caps">Call Us:</span><br>+1 555-014-2200</div>

<div class="abs hero-title caps">Selling Cruises</div>
<div class="abs hero-copy">Embark on the voyage of a lifetime with the most exquisite cruise destinations, tailored experiences, and unbeatable offers.</div>
<div class="abs hero-rule"></div>
<div class="abs pill hero-btn"><span class="ring"></span>Find your perfect cruise today!</div>

<div class="abs search"></div>
<div class="abs field" style="left:125px;width:279px">Search for cruise Destinations
  <svg class="abs" style="right:14px" width="22" height="22" viewBox="0 0 22 22"><circle cx="9" cy="9" r="7" fill="none" stroke="#222" stroke-width="1.6"/><path d="M14 14l6 6" stroke="#222" stroke-width="1.6"/></svg>
</div>
<div class="abs field" style="left:417px;width:279px">Date
  <svg class="abs" style="right:14px" width="20" height="20" viewBox="0 0 20 20"><rect x="1" y="3" width="18" height="16" rx="2" fill="none" stroke="#222" stroke-width="1.4"/><path d="M1 8h18M5 1v4M15 1v4M5 11h2M9 11h2M13 11h2M5 15h2M9 15h2M13 15h2" stroke="#222" stroke-width="1.4"/></svg>
</div>
<div class="abs field" style="left:714px;width:280px">Type of  Ship
  <svg class="abs" style="right:16px" width="22" height="14" viewBox="0 0 22 14"><path d="M2 2l9 9 9-9" fill="none" stroke="#222" stroke-width="2.4"/></svg>
</div>
<div class="abs search-go">
  <svg width="57" height="57" viewBox="0 0 57 57"><circle cx="27" cy="27" r="11" fill="none" stroke="#fff" stroke-width="2"/><path d="M35 35l7 7" stroke="#fff" stroke-width="2"/></svg>
</div>

<div class="abs dot welcome-dot"></div>
<div class="abs welcome-title caps">Welcome <span>To Glacia</span></div>
<div class="abs welcome-copy">Embark on the voyage of a lifetime with the most exquisite cruise destinations, tailored experiences, and unbeatable offers. Whether you're seeking a relaxing tropical getaway, an adventurous Antarctic expedition, or a cultural journey through the Galápagos Islands, we have something for every traveler. Explore world-class cruise options with a variety of amenities, destinations, and cruise lines that will make your trip unforgettable. Get ready to sail toward your next adventure!</div>
<div class="abs pill read-btn"><span class="ring"></span>Read More</div>

<!-- FEATURED -->
<div class="abs dot" style="top:1146px"></div>
<div class="abs sec-title caps" style="top:1182px">Featured <span>Selling Cruises</span></div>

<div class="abs card" style="left:112px;background:var(--blue)">
  <div class="photo" role="img" aria-label="Red expedition ship breaking through polar ice" style="background:linear-gradient(160deg,#9ab8d4,#d8e2ea 45%,#b8303a 60%,#e9eef2 80%,#7e9bb3)"></div>
  <div class="body"><h3 class="caps">Best Antarctic Cruises</h3>
  <p>Experience the untouched beauty of Antarctica with expert-guided expeditions to the most pristine wilderness on Earth.</p>
  <div class="price caps">Starting from<br>$X,XXX per person</div></div>
</div>
<div class="abs card" style="left:442px;background:var(--navy)">
  <div class="photo" role="img" aria-label="Volcanic Galápagos island with turquoise bays" style="background:linear-gradient(175deg,#8fb3d0 0%,#a48a6a 35%,#8c5a3c 60%,#3fa3b6 85%,#2a6f8d)"></div>
  <div class="body"><h3 class="caps">Top Galápagos Cruises</h3>
  <p>Discover the unique wildlife and natural wonders of the Galápagos Islands on an unforgettable journey.</p>
  <div class="price caps">Starting from<br>$X,XXX per person</div></div>
</div>
<div class="abs card" style="left:773px;background:var(--blue)">
  <div class="photo" role="img" aria-label="Business handshake at a harbour at sunset" style="background:linear-gradient(100deg,#2c3040,#c98a48 45%,#f0c070 55%,#3a4050)"></div>
  <div class="body"><h3 class="caps">Last-Minute Deals</h3>
  <p>Don't miss out on incredible discounts for last-minute cruise bookings.</p>
  <div class="price caps">Starting from<br>$X,XXX per person</div></div>
</div>

<!-- DESTINATIONS -->
<div class="abs dest-band"></div>
<div class="abs dot" style="top:1940px"></div>
<div class="abs sec-title caps" style="top:1975px"><span>Our</span> Destinations</div>

<div class="abs dest" style="left:112px"><div class="photo" role="img" aria-label="Caribbean island coastline" style="background:linear-gradient(170deg,#a9c2d8,#5f8a5a 45%,#2fb3b8 75%,#1f8aa0)"></div><div class="name caps">Caribbean</div></div>
<div class="abs dest" style="left:357px"><div class="photo" role="img" aria-label="Mediterranean cliffside village" style="background:linear-gradient(170deg,#b98a5a,#e7d2b8 45%,#c98a60 65%,#3f8fb3)"></div><div class="name caps">Mediterranean</div></div>
<div class="abs dest" style="left:603px"><div class="photo" role="img" aria-label="Alaskan waterfront houses among pines" style="background:linear-gradient(175deg,#7fb0cf,#2f5a3a 40%,#6b7f8f 65%,#2f5f70)"></div><div class="name caps">Alaska</div></div>
<div class="abs dest" style="left:849px"><div class="photo" role="img" aria-label="Asian temple on a lake" style="background:linear-gradient(175deg,#5f8fc0,#e6d3b0 35%,#3f6a4a 60%,#4f86b0)"></div><div class="name caps">Asia</div></div>

<!-- CRUISE LINE -->
<div class="abs line-panel"></div>
<div class="abs line-photo" role="img" aria-label="Aerial view of a large cruise ship at sea"></div>
<div class="abs dot" style="left:114px;top:2494px"></div>
<div class="abs line-title caps">Cruise Line</div>
<div class="abs line-copy">Lorem ipsum dolor sit amet, consectetur adipiscing elit, sed do eiusmod tempor incididunt ut labore et dolore magna aliqua. Ut enim ad minim veniam, quis nostrud exercitation ullamco laboris nisi ut aliquip ex ea commodo consequat. Duis aute irure dolor in reprehenderit in voluptate velit esse cillum dolore eu fugiat nulla pariatur. uis nostrud exercitation ullamco laboris nisi ut aliquip ex ea commodo consequat. Duis aute irure dolor in</div>
<div class="abs pill line-btn"><span class="ring"></span>Read More</div>

<!-- TESTIMONIALS -->
<div class="abs dot" style="top:3097px"></div>
<div class="abs sec-title caps" style="top:3134px"><span>Customer</span> Testimonials</div>

<div class="abs quote" style="left:111px">
  <div class="face" role="img" aria-label="Portrait photo of the customer"></div>
  <div class="stars">★★★★★</div>
  <p>The best vacation I've ever had! The staff was so attentive, and the ship was beautiful. Highly recommend the Mediterranean cruise!"</p>
  <div class="who">Lena K</div><div class="role">Verified Passenger</div>
</div>
<div class="abs quote" style="left:611px">
  <div class="face" role="img" aria-label="Portrait photo of the customer" style="background:linear-gradient(160deg,#e8e8e8,#9a9a9a)"></div>
  <div class="stars">★★★★★</div>
  <p>We had an amazing experience on our Alaskan adventure! The sights were breathtaking, and the excursions were top-notch. A must-do!</p>
  <div class="who">Marco D</div><div class="role">Verified Passenger</div>
</div>

<!-- FOOTER -->
<div class="abs footer" role="img" aria-label="Faded cruise ship at sea in dark blue tones"></div>
<div class="abs dot" style="top:3591px"></div>
<div class="abs sec-title caps foot-title" style="top:3640px"><span>Newsletter</span> Subscription Form</div>
<div class="abs news-input caps">Join our exclusive newsletter</div>
<div class="abs pill news-btn"><span class="ring"></span>Sign up Now</div>
<div class="abs chat" aria-label="Chat with us"></div>

<div class="abs foot-brand">Glacia.co</div>

<div class="abs foot-nav caps" style="left:220px">Home</div>
<div class="abs foot-nav caps" style="left:308px">Cruise Lines</div>
<div class="abs foot-nav caps" style="left:445px">Destinations</div>
<div class="abs foot-nav caps" style="left:585px">Itineraries</div>
<div class="abs foot-nav caps" style="left:716px">Blog</div>
<div class="abs foot-nav caps" style="left:801px">About Us</div>
<div class="abs foot-nav caps" style="left:918px">Contact</div>

<div class="abs legal caps" style="left:117px">Copyright 2025 Company Name All Rights Reserved</div>
<div class="abs legal caps" style="left:842px">FAQ</div>
<div class="abs legal caps" style="left:908px">Privacy Policy</div>
<div class="abs legal caps" style="left:1048px">Terms</div>

</body>
</html>
```